MarbleTrove - New Website Design

Create a professional Vendora website for the hottest trend; a box of school supplies subscription box business called MarbleTrove. Vendora.com is an easy to use website builder.
Please see fizwickpod.com; plumfolly.com; tarrowmintloft.com; and nipcove.com for the concept I am after. The business has not been launched yet, I am currently in the pre-launch stage using a specialized landing page website, and so the time scale for developing my professional looking Vendora website is up to 1-2 weeks.
The webpage should have a fun feel and should match the style of the company logo at plumfolly.com. The pages to include are 'Home', 'About us' and 'Get Started'
Thank you and good luck!
1 page

```html
<!DOCTYPE html>
<html lang="en">
<head>
<meta charset="utf-8">
<title>MarbleTrove</title>
<link href="https://fonts.googleapis.com/css2?family=Mulish:ital,wght@0,400;0,600;0,700;1,400&display=swap" rel="stylesheet">
<style>
:root{
  --green:#7cb82f;
  --orange:#f58220;
  --ink:#2e2e2e;
  --grey:#777;
  --dark:#2b2b2b;
  --panel:#a9a9a9;
  --footer:#ececec;
  --white:#fff;
}
*{box-sizing:border-box;margin:0;padding:0}
html,body{width:1200px;height:4534px;overflow:hidden}
body{font-family:'Mulish',sans-serif;color:var(--ink);background:var(--white);position:relative}
section,footer{position:absolute;left:0;width:1200px;overflow:hidden}
.abs{position:absolute}
.center{text-align:center;left:0;width:100%}
.fill{position:absolute}

/* hero */
.hero{top:0;height:629px}
.hero .fill{inset:0;background:linear-gradient(135deg,#6b6055 0%,#4a4744 45%,#5d4a52 75%,#3c3a3a 100%)}
.menu-icon{left:115px;top:50px}
.brand{top:46px;font-size:30px;font-weight:700;color:var(--white);letter-spacing:.5px}
.cart-icon{left:1040px;top:42px}
.hero-title{top:248px;font-size:38px;line-height:50px;color:var(--white);font-weight:400}
.dots{top:586px;left:556px;display:flex;gap:9px}
.dots span{width:14px;height:14px;border-radius:50%;background:var(--white);opacity:.9}
.dots span:first-child{background:transparent;border:2px solid var(--white)}

/* about */
.about{top:629px;height:414px}
.about .fill{left:136px;top:21px;width:424px;height:348px;background:linear-gradient(180deg,#cfc3b0 0%,#b88c58 55%,#9a6e3e 100%);border-radius:4px}
.rule{height:3px;background:var(--orange);width:80px}
.about .rule{left:587px;top:97px;background:#999}
.about h2{left:587px;top:108px;font-size:36px;font-weight:400;color:var(--green)}
.about .copy{left:587px;top:171px;width:445px}
.copy p{font-size:14px;line-height:22px;color:var(--grey);margin-bottom:12px}

/* video band */
.video{top:1043px;height:478px}
.video .fill{inset:0;background:linear-gradient(120deg,#4e5a3a 0%,#6b6248 40%,#3d4a66 75%,#50413a 100%)}
.video blockquote{top:135px;font-size:26px;line-height:38px;color:var(--white);padding:0 230px}
.play{left:550px;top:225px}

/* why */
.why{top:1521px;height:338px}
.why .rule{left:560px;top:75px}
.why h2{top:95px;font-size:30px;font-weight:400}
.why .copy{top:150px;left:270px;width:660px;text-align:center}

/* tiles */
.tiles{top:1859px;height:445px}
.tile{position:absolute;top:0;width:600px;height:445px;display:flex;flex-direction:column;align-items:center;justify-content:center;gap:14px;color:var(--white);font-size:25px;letter-spacing:.5px}
.tile.brands{left:0;background:linear-gradient(135deg,#f7931e 0%,#f07c14 50%,#f5a623 100%)}
.tile.quality{left:600px;background:linear-gradient(135deg,#3a3a3a 0%,#4e4e4e 50%,#2e2e2e 100%)}
.tile span{margin-top:6px}

/* testimonial */
.testimonial{top:2304px;height:302px;background:var(--dark);color:var(--white)}
.testimonial blockquote{top:100px;font-size:20px;line-height:36px;font-style:italic}
.testimonial cite{top:176px;font-style:normal;font-weight:700;font-size:21px}

/* school box */
.featured{top:2606px;height:614px}
.featured .lead{top:108px;font-size:19px;line-height:32px;color:#555;padding:0 230px}
.card{left:302px;top:266px;width:605px;height:284px;border:2px solid #999}
.featured .fill{left:187px;top:281px;width:310px;height:251px;background:linear-gradient(180deg,#4f7fc4 0%,#e05b6f 40%,#e8d28a 65%,#c9a66b 100%);border-radius:4px}
.featured h3{left:514px;top:325px;font-size:28px;font-weight:400}
.featured .copy{left:514px;top:370px;width:385px}
.featured .copy p{font-size:12px;line-height:19px}
.btn{display:block;color:var(--white);text-align:center;font-weight:700;font-size:14px;letter-spacing:.5px}
.btn.buy{left:514px;top:462px;width:139px;height:40px;line-height:40px;background:var(--green)}

/* choose */
.choose{top:3220px;height:462px}
.choose .photo{left:0;top:0;width:610px;height:462px;background:linear-gradient(135deg,#8a98a8 0%,#b8c2cc 40%,#7d8c6f 75%,#5b6a7a 100%)}
.choose .side{position:absolute;left:610px;top:0;width:590px;height:462px;background:var(--panel)}
.choose h2{left:410px;width:400px;text-align:center;top:185px;font-size:30px;font-weight:400;color:var(--white)}
.choose .box{left:725px;top:90px;width:318px;height:212px;background:linear-gradient(180deg,#c89a5b 0%,#2f2b33 20%,#d94b6d 55%,#4aa0d8 80%,#c89a5b 100%);border-radius:3px}
.choose .box-title{left:610px;width:590px;text-align:center;top:322px;font-size:20px;color:var(--white)}
.btn.click{left:795px;top:365px;width:136px;height:33px;line-height:33px;background:var(--orange);font-size:13px}

/* packages */
.packages{top:3682px;height:514px}
.packages .fill{left:151px;top:66px;width:439px;height:418px;background:linear-gradient(180deg,#4a7ec0 0%,#5ba85a 25%,#c79a62 55%,#a57642 100%);border-radius:4px}
.packages h2{left:653px;top:102px;font-size:34px;font-weight:400}
.price{left:683px;top:165px;font-size:22px}
.price .now{color:var(--orange)}
.price .dash{color:#bbb;margin:0 16px}
.price .was{color:#888;text-decoration:line-through}
.select{left:662px;width:242px;height:30px;background:#f1f1f1;border:1px solid #ddd;font-size:12px;color:#555;display:flex;align-items:center;padding:0 12px}
.select .label{width:110px}
.select .val{flex:1}
.btn.cart{left:662px;top:318px;width:242px;height:42px;line-height:42px;background:var(--green);font-size:14px}
.links{left:690px;top:378px;display:flex;gap:42px;font-size:11px;color:#666;letter-spacing:.5px}

/* footer */
.site-footer{top:4196px;height:338px;background:var(--footer)}
.nav-links{left:166px;top:58px;list-style:none}
.nav-links li{font-size:16px;line-height:35px;color:#333;letter-spacing:.4px}
.signup{left:553px;top:50px;font-size:20px;color:#333;letter-spacing:.4px}
.email{left:553px;top:108px;width:452px;height:36px;border-bottom:1px solid #888;display:flex;justify-content:space-between;align-items:center;font-size:14px;color:#444}
.social{left:160px;top:252px;display:flex;gap:12px;font-size:12px;color:#333}
.social span{display:flex;align-items:center;gap:4px}
.social i{width:10px;height:10px;border:1.5px solid #333;border-radius:50%;display:inline-block}
.copyright{left:499px;top:253px;font-size:12px;color:#555}
.payments{left:860px;top:253px;display:flex;gap:14px;font-size:12px;font-weight:700;color:#666}
</style>
</head>
<body>

<section class="hero">
  <div class="fill" role="img" aria-label="Photo of school supplies: colourful pencils, notebooks and scissors on a desk"></div>
  <svg class="abs menu-icon" width="42" height="24" viewBox="0 0 42 24"><g stroke="#fff" stroke-width="3"><line x1="0" y1="2" x2="42" y2="2"/><line x1="0" y1="12" x2="42" y2="12"/><line x1="0" y1="22" x2="42" y2="22"/></g></svg>
  <div class="abs center brand">MARBLETROVE</div>
  <svg class="abs cart-icon" width="40" height="36" viewBox="0 0 40 36"><path d="M12 12 V8 a8 8 0 0 1 16 0 V12" fill="none" stroke="#fff" stroke-width="3"/><path d="M2 12 H38 L35 34 H5 Z" fill="#fff"/></svg>
  <h1 class="abs center hero-title">Vivamus porttitor purus nisi eleifend<br>libero tempus libero lectus</h1>
  <div class="abs dots"><span></span><span></span><span></span><span></span></div>
</section>

<section class="about">
  <div class="fill" role="img" aria-label="Photo of an open cardboard box filled with pencils, scissors and school tools"></div>
  <div class="abs rule"></div>
  <h2 class="abs">About MarbleTrove</h2>
  <div class="abs copy">
    <p>Praesent elementum elit at tellus nec ultricies sit amet porttitor mattis enim in massa libero interdum nec</p>
    <p>Interdum vel blandit sed nulla in ullamcorper est eget tempor cursus neque mi consectetuer mi a ultricies massa est sed nisi Class aptent taciti sociosqu ad litora torquent per conubia nostra per inceptos hymenaeos Proin nulla arcu nonumm</p>
  </div>
</section>

<section class="video">
  <div class="fill" role="img" aria-label="Photo of paint sets, markers and pencil cups on a green table"></div>
  <blockquote class="abs center">"Fusce ultricies orci ac feugiat suscipit leo massa sodales velit et scelerisque mi tortor at ipsum cligula augue"</blockquote>
  <svg class="abs play" width="100" height="100" viewBox="0 0 100 100"><circle cx="50" cy="50" r="46" fill="none" stroke="#fff" stroke-width="4"/><path d="M40 30 L70 50 L40 70 Z" fill="#fff"/></svg>
</section>

<section class="why">
  <div class="abs rule"></div>
  <h2 class="abs center">Why Choose Our Box</h2>
  <div class="abs copy">
    <p>Praesent elementum elit at tellus nec ultricies sit amet porttitor mattis enim in massa</p>
    <p>Interdum vel blandit sed nulla in ullamcorper est eget tempor cursus neque mi consectetuer mi a ultricies massa est sed nisi Class aptent taciti sociosqu ad litora torquent per conubia nostra per inceptos hymenaeos Proin nulla arcu nonumm</p>
  </div>
</section>

<section class="tiles">
  <div class="tile brands" role="img" aria-label="Orange tinted photo of rulers and stationery">
    <svg width="70" height="70" viewBox="0 0 70 70"><circle cx="35" cy="35" r="31" fill="none" stroke="#fff" stroke-width="4"/><path d="M21 36 L31 46 L50 25" fill="none" stroke="#fff" stroke-width="5"/></svg>
    <span>TOP BRANDS</span>
  </div>
  <div class="tile quality" role="img" aria-label="Dark tinted photo of notebooks, ink and office supplies">
    <svg width="70" height="70" viewBox="0 0 70 70"><circle cx="35" cy="35" r="31" fill="none" stroke="#fff" stroke-width="4"/><path d="M21 36 L31 46 L50 25" fill="none" stroke="#fff" stroke-width="5"/></svg>
    <span>QUALITY PRODUCTS</span>
  </div>
</section>

<section class="testimonial">
  <blockquote class="abs center">“Class aptent taciti sociosqu ad litora torquent per conubia nostra per inceptos<br>“hymenaeos Proin nulla arcu nonummy luctus dictum ege”</blockquote>
  <cite class="abs center">By Author Name</cite>
</section>

<section class="featured">
  <p class="abs center lead">Morbi diam mauris viverra in gravida eu mattis in ante Morbi eget arcu Morbi porta libero id ullamcorper nonummy nibh ligula pulvinar metus eget</p>
  <div class="abs card"></div>
  <div class="fill" role="img" aria-label="Photo of a wooden crate full of colourful school supplies labelled School Box"></div>
  <h3 class="abs">School Box</h3>
  <div class="abs copy">
    <p>Ullamcorper est eget tempor cursus neque mi consectetuer mi a ultricies massa est sed nisi Class aptent taciti sociosqu ad litora torquent</p>
  </div>
  <a class="abs btn buy">BUY NOW</a>
</section>

<section class="choose">
  <div class="fill photo" role="img" aria-label="Photo of children drawing with crayons at a table"></div>
  <div class="side"></div>
  <h2 class="abs">Choose Your Box</h2>
  <div class="fill box" role="img" aria-label="Photo of an open wooden art case with markers and pencils"></div>
  <div class="abs box-title">Your Box Tittle here</div>
  <a class="abs btn click">CLICK HERE</a>
</section>

<section class="packages">
  <div class="fill" role="img" aria-label="Photo of a cardboard box with a globe, pencils and school tools"></div>
  <h2 class="abs">Our Box Packages</h2>
  <div class="abs price"><span class="now">$140.00</span><span class="dash">-</span><span class="was">$550.00</span></div>
  <div class="abs select" style="top:236px"><span class="label">For Class :</span><span class="val">5th</span><span>⌄</span></div>
  <div class="abs select" style="top:281px"><span class="label">Products :</span><span class="val">25</span><span>⌄</span></div>
  <a class="abs btn cart">ADD TO CART</a>
  <div class="abs links"><span>☰ FULL DETAIL</span><span>⇪ SHARE</span></div>
</section>

<footer class="site-footer">
  <ul class="abs nav-links">
    <li>CONTACT US</li>
    <li>TERM OF USE</li>
    <li>PRIVACY</li>
    <li>SITEMAP</li>
  </ul>
  <div class="abs signup">SIGN UP FOR UPDATES</div>
  <div class="abs email"><span>Email address</span><span>OK</span></div>
  <div class="abs social"><span><i></i>Quillo</span><span><i></i>Fernly</span><span><i></i>Daskit</span><span><i></i>Mopple</span></div>
  <div class="abs copyright">© 2017 Company Name &nbsp;All right reserved</div>
  <div class="abs payments"><span>Plenqo</span><span>Zarvil</span><span>Quopa</span><span>Vexmint</span></div>
</footer>

</body>
</html>
```